Web design project for exciting Australian start-up

Background
We are looking for a creative and talented web design artist to work alongside our market leading web developer.
• You will be required to create a modern and clean design theme for our website, incorporating selected rustic colour scheme elements for our exciting Australian start-up to operate within the coffee industry.
reoccurring work to be expected to flow to the successful designer.
Requirements
• c. 5 - 10 page website
• Landing page
• Log in/ out
• 404 template
• Typography is emphasised
• Please use either a) typemarrow.com, b) free web fonts, c) brindle fonts
• All design elements in vector format
• Preferably with icons for each header title(i.e. about us, how it works etc) but designer have free reign over how the site looks, so might not be applicable
• All pages to be responsive
• Down to eSlab resolution

High level visual design brief attached - additional pages to be worked from base design.

Design inspiration
• We would like to use design elements from the following sources:
http://www.zandrix.com/halcyon/ (Functionality)
Colour scheme refer to logo and complementary style guide

```html
<!DOCTYPE html>
<html lang="en">
<head>
<meta charset="utf-8">
<title>Bean Harbour — Marketplace</title>
<link rel="stylesheet" href="https://fonts.googleapis.com/css2?family=Open+Sans:wght@700&family=Roboto+Slab:wght@300;400&display=swap">
<style>
  :root{
    --red:#e8383d;
    --orange:#f99c34;
    --ink:#1a1a1a;
    --text:#444;
    --rule:#ececec;
    --footer-bg:#e8e8e8;
    --bar-bg:#4a4a4a;
    --white:#fff;
  }
  *{box-sizing:border-box;margin:0;padding:0}
  html,body{width:1200px;height:950px;overflow:hidden;background:var(--white)}
  body{font-family:"Roboto Slab",Georgia,serif;color:var(--text);position:relative}

  .site-header{position:absolute;top:0;left:0;width:1200px;height:107px;background:var(--white)}
  .brand{position:absolute;left:161px;top:34px;display:flex;align-items:center;gap:10px;
    font-family:"Roboto Slab",serif;font-weight:400;font-size:26px;letter-spacing:2px;color:var(--ink)}
  .brand-mark{width:34px;height:34px;border-radius:50%;background:var(--orange)}

  .main-nav{position:absolute;left:423px;top:0;height:107px;display:flex}
  .nav-item{height:107px;border-left:1px solid var(--rule);display:flex;flex-direction:column;
    align-items:center;justify-content:center;gap:6px;font-size:12px;color:#333;text-transform:uppercase;font-weight:300}
  .nav-item:last-child{border-right:1px solid var(--rule)}
  .nav-item svg{width:20px;height:20px}
  .nav-about{width:94px}.nav-how{width:135px}.nav-faq{width:66px}

  .account-actions{position:absolute;top:38px;left:750px;display:flex;gap:9px}
  .btn{height:32px;display:flex;align-items:center;justify-content:center;color:var(--white);
    font-size:14px;font-weight:300;border-radius:2px}
  .btn-red{background:var(--red)}
  .btn-orange{background:var(--orange)}
  .btn-account{width:119px}.btn-login{width:76px}.btn-signup{width:76px}

  .hero{position:absolute;top:107px;left:0;width:1200px;height:543px;
    background:
      radial-gradient(ellipse 420px 220px at 600px 560px,#8a4a1e 0%,#3a1b08 55%,transparent 80%),
      radial-gradient(ellipse 360px 300px at 560px 180px,#a5541f 0%,#4a2208 50%,transparent 80%),
      #050302}
  .hero-title{position:absolute;top:218px;width:100%;text-align:center;font-family:"Open Sans",sans-serif;
    font-weight:700;font-size:36px;color:var(--white);letter-spacing:.5px}
  .btn-tender{position:absolute;left:519px;top:276px;width:162px;height:46px;font-size:18px;border-radius:2px}

  .site-footer{position:absolute;top:650px;left:0;width:1200px;height:236px;background:var(--footer-bg)}
  .footer-col{position:absolute;top:50px}
  .footer-col h3{font-family:"Roboto Slab",serif;font-weight:400;font-size:18px;color:var(--ink);letter-spacing:.5px;margin-bottom:14px}
  .footer-col ul{list-style:none}
  .footer-col li{font-size:14px;font-weight:300;color:#555;height:31px;display:flex;align-items:center}
  .col-info{left:295px}.col-who{left:541px}.col-who ul{padding-left:3px}.col-social{left:798px}
  .col-social li{padding-left:3px;width:100px;justify-content:space-between}
  .social-dot{width:10px;height:10px;background:#555;border-radius:2px}

  .bottom-bar{position:absolute;top:886px;left:0;width:1200px;height:64px;background:var(--bar-bg)}
  .bottom-bar .rule{position:absolute;top:5px;left:161px;width:878px;height:1px;background:#666}
  .copyright{position:absolute;top:24px;width:100%;text-align:center;color:var(--white);font-size:14px;font-weight:300}
</style>
</head>
<body>
  <header class="site-header">
    <div class="brand"><span class="brand-mark"></span>BEAN HARBOUR</div>
    <nav class="main-nav">
      <div class="nav-item nav-about">
        <svg viewBox="0 0 20 20" fill="none" stroke="#f99c34" stroke-width="1.3"><path d="M2 10 L10 3 L18 10"/><path d="M4.5 8.5 V17 H15.5 V8.5"/><path d="M8.5 17 V12 H11.5 V17"/></svg>
        About Us
      </div>
      <div class="nav-item nav-how">
        <svg viewBox="0 0 20 20" fill="none" stroke="#555" stroke-width="1.2"><circle cx="8" cy="8" r="3"/><path d="M3 18 C3 13 13 13 13 18"/><rect x="12" y="2" width="6" height="5"/></svg>
        How it works
      </div>
      <div class="nav-item nav-faq">
        <svg viewBox="0 0 20 20" fill="none" stroke="#555" stroke-width="1.2"><rect x="4" y="5" width="4" height="13"/><rect x="11" y="2" width="5" height="16"/></svg>
        FAQ
      </div>
    </nav>
    <div class="account-actions">
      <span class="btn btn-red btn-account">My Account</span>
      <span class="btn btn-orange btn-login">Login</span>
      <span class="btn btn-red btn-signup">Sign up</span>
    </div>
  </header>

  <section class="hero" role="img" aria-label="Roasted coffee beans heaped under rising smoke on a dark background">
    <h1 class="hero-title">MARKETPLACE</h1>
    <span class="btn btn-orange btn-tender">Start a Tender</span>
  </section>

  <footer class="site-footer">
    <div class="footer-col col-info">
      <h3>HELPFUL INFO</h3>
      <ul><li>About Us</li><li>Media Enquiries</li><li>Terms &amp; Conditions</li><li>Privacy Policy</li></ul>
    </div>
    <div class="footer-col col-who">
      <h3>WHO WE ARE</h3>
      <ul><li>How it works</li><li>FAQ</li><li>Contact us</li></ul>
    </div>
    <div class="footer-col col-social">
      <h3>JOIN US ON</h3>
      <ul>
        <li>Friendloop<span class="social-dot"></span></li>
        <li>Chirpline<span class="social-dot"></span></li>
        <li>WorkNet<span class="social-dot"></span></li>
        <li>ClipStream<span class="social-dot"></span></li>
      </ul>
    </div>
  </footer>

  <div class="bottom-bar">
    <div class="rule"></div>
    <p class="copyright">Copyright © 2014 Bean Harbour</p>
  </div>
</body>
</html>
```